Bref créative
Stationary Design for Real Estate Business
Business Card, Letterhead, Envelope Design
Professional
Derek Halvorsen
Broker/Owner
418 Brantley Avenue
Mooresville, NC 28342
derek@harwoodestatesvc.com
www.HarwoodEstateSvc.com
We need the following designed as part of this stationary package: business card, letterhead, envelopes, 9"x12" pocket folder, and fax sheets.
Adobe Illustrator file for our logo
eps file for our logo
png file for our logo

```html
<!DOCTYPE html>
<html lang="en">
<head>
<meta charset="utf-8">
<title>Harwood Estate Services — Stationery</title>
<link rel="stylesheet" href="https://fonts.googleapis.com/css2?family=Libre+Baskerville:wght@400;700&family=Open+Sans:wght@400;600&display=swap">
<style>
  :root{
    --backdrop:#e6dac6;
    --paper:#ffffff;
    --navy:#1d3449;
    --teal:#2f6f8f;
    --teal-dark:#1b4a66;
    --slate:#5f6a73;
    --slate-dark:#3e474e;
    --ink:#5a6570;
    --label:#6b5d4a;
    --shadow:0 2px 6px rgba(60,45,25,.28);
  }
  *{box-sizing:border-box;margin:0;padding:0}
  html,body{width:1200px;height:446px;overflow:hidden}
  body{background:var(--backdrop);font-family:"Open Sans",Arial,sans-serif;position:relative}
  .sheet{position:absolute;background:var(--paper);box-shadow:var(--shadow)}
  .label{position:absolute;font-family:"Libre Baskerville",Georgia,serif;font-size:7px;letter-spacing:.12em;text-transform:uppercase;color:var(--label);white-space:nowrap}
  .brand{display:flex;align-items:center;gap:5px}
  .brand-dot{border-radius:50%;background:var(--teal);flex:none}
  .brand-name{font-family:"Libre Baskerville",Georgia,serif;font-weight:700;color:var(--navy);line-height:1}
  .brand-tag{font-size:4px;letter-spacing:.2em;text-transform:uppercase;color:var(--ink);margin-top:2px}
  .watermark{position:absolute;border-radius:50%;background:radial-gradient(circle,rgba(47,111,143,.14),rgba(47,111,143,.04) 70%,transparent 72%)}
  .contact{position:absolute;font-size:4.2px;line-height:6px;color:var(--ink)}
  .footer-bar{position:absolute;left:0;right:0;height:14px;background:linear-gradient(90deg,var(--teal-dark),var(--teal));color:#e7f1f6;font-size:4px;display:flex;align-items:center;padding-left:70px}
  .card-blue{position:absolute;top:0;bottom:0;right:0;width:46%;background:linear-gradient(135deg,var(--teal),var(--teal-dark))}
  .env-flap{position:absolute;left:0;right:0;top:0}
</style>
</head>
<body>

<div class="label" style="left:19px;top:174px">Stationary Designs</div>

<!-- business card front -->
<div class="sheet card-front" style="left:19px;top:226px;width:79px;height:46px">
  <div class="brand" style="position:absolute;left:5px;top:17px">
    <span class="brand-dot" style="width:6px;height:6px"></span>
    <div><div class="brand-name" style="font-size:7px">Harwood</div></div>
  </div>
  <div class="card-blue">
    <div style="position:absolute;left:4px;top:10px;font-size:3px;line-height:4.5px;color:#d9ebf3">Derek Halvorsen<br>Broker/Owner<br>418 Brantley Avenue<br>derek@harwoodestatesvc.com</div>
  </div>
</div>
<div class="label" style="left:19px;top:277px;font-size:5.5px">Business Card Front</div>

<!-- business card back -->
<div class="sheet card-back" style="left:19px;top:305px;width:79px;height:46px">
  <div class="brand" style="position:absolute;left:14px;top:17px">
    <span class="brand-dot" style="width:7px;height:7px"></span>
    <div><div class="brand-name" style="font-size:9px">Harwood</div></div>
  </div>
</div>
<div class="label" style="left:19px;top:356px;font-size:5.5px">Business Card Back</div>

<!-- letterhead option 1 -->
<div class="sheet letterhead" style="left:156px;top:6px;width:305px;height:422px">
  <div class="brand" style="position:absolute;left:22px;top:18px">
    <span class="brand-dot" style="width:13px;height:13px"></span>
    <div><div class="brand-name" style="font-size:15px">Harwood</div><div class="brand-tag">Estate Services</div></div>
  </div>
  <div class="contact" style="left:150px;top:18px">418 Brantley Avenue<br>Mooresville, NC 28342<br>Phone 704.555.0142<br>Fax 704.555.0143<br>derek@harwoodestatesvc.com<br>www.HarwoodEstateSvc.com</div>
  <div class="watermark" role="img" aria-label="Faint brand emblem watermark" style="left:102px;top:210px;width:100px;height:100px"></div>
</div>
<div class="label" style="left:262px;top:434px;font-size:5.5px">Letterhead Option 1</div>

<!-- letterhead option 2 -->
<div class="sheet letterhead" style="left:480px;top:6px;width:300px;height:394px">
  <div class="brand" style="position:absolute;left:0;right:0;top:20px;justify-content:center">
    <span class="brand-dot" style="width:11px;height:11px"></span>
    <div><div class="brand-name" style="font-size:13px">Harwood</div><div class="brand-tag">Estate Services</div></div>
  </div>
  <div class="watermark" role="img" aria-label="Faint brand emblem watermark" style="left:96px;top:130px;width:110px;height:110px"></div>
  <div class="footer-bar" style="bottom:14px">418 Brantley Avenue · Mooresville, NC 28342 · www.HarwoodEstateSvc.com</div>
</div>
<div class="label" style="left:585px;top:426px;font-size:5.5px">Letterhead Option 2</div>

<!-- envelopes -->
<div class="sheet envelope" style="left:815px;top:6px;width:385px;height:115px;background:linear-gradient(180deg,var(--teal),var(--teal-dark))"></div>
<div class="sheet envelope" style="left:815px;top:95px;width:385px;height:130px;background:#f3f3f3;overflow:hidden">
  <svg class="env-flap" width="385" height="80" viewBox="0 0 385 80"><path d="M0 0H385V22Q385 34 365 40L200 78Q192 80 184 78L20 40Q0 34 0 22Z" fill="var(--slate)"/></svg>
</div>
<div class="sheet envelope" style="left:815px;top:175px;width:385px;height:90px;overflow:hidden">
  <svg class="env-flap" width="385" height="50" viewBox="0 0 385 50"><path d="M0 0L192 40L385 0" fill="none" stroke="#d8d8d8" stroke-width="1"/></svg>
  <div class="brand" style="position:absolute;left:0;right:0;top:30px;justify-content:center">
    <span class="brand-dot" style="width:9px;height:9px"></span>
    <div class="brand-name" style="font-size:11px">Harwood</div>
  </div>
</div>
<div class="sheet envelope" style="left:792px;top:240px;width:265px;height:146px;overflow:hidden">
  <div class="brand" style="position:absolute;left:10px;top:44px">
    <span class="brand-dot" style="width:9px;height:9px"></span>
    <div><div class="brand-name" style="font-size:10px">Harwood</div><div class="brand-tag">Estate Services</div></div>
  </div>
  <div class="watermark" role="img" aria-label="Faint brand emblem watermark" style="left:120px;top:50px;width:90px;height:90px"></div>
</div>
<div class="label" style="left:1090px;top:416px;font-size:5.5px">Envelope Design</div>

</body>
</html>
```